Industrial Project Sign

We need an eye catching (but professional) industrial project sign that will be very large (roughly 12' high x 18' wide). This sign will be highly visible from the adjacent high speed highway.

* The following needs to be at the bottom of the signage: Logo (uploaded), Name (Brightline Property Partners, Inc.) (uploaded) and phone number (415)736-2958

*Name of Project - "Meridale Commerce Park"

* Text items
Land for Sale
Build to Suit
Zoning: Industrial (G I & L I)

* Interesting background that is eye catching
Updates

Good morning all,

We are considering all designers options as we go and are waiting for the final designs to come in by the 4th so that we can give each one a good look.   If you have any new designs, questions, further design options or any tweeks you want to do to current designs, please do so at this time.

Thanks to all of you for your submissions.

Industry/Entity Type

Industrial

```html
<!DOCTYPE html>
<html lang="en">
<head>
<meta charset="utf-8">
<title>Meridale Commerce Park – Project Sign</title>
<link href="https://fonts.googleapis.com/css2?family=Josefin+Sans:wght@600;700&display=swap" rel="stylesheet">
<style>
  :root {
    --sky: #29a9e0;
    --sky-light: #41c5f3;
    --navy: #2f3079;
    --magenta: #d7118b;
    --mist: #eef1f9;
    --white: #ffffff;
  }
  html, body {
    margin: 0;
    padding: 0;
    width: 1200px;
    height: 800px;
    overflow: hidden;
    background: var(--white);
  }
  .sign {
    position: relative;
    width: 1200px;
    height: 800px;
    overflow: hidden;
    font-family: "Josefin Sans", "Century Gothic", sans-serif;
    background: var(--sky);
  }
  .backdrop {
    position: absolute;
    inset: 0;
  }
  .project-title {
    position: absolute;
    left: 48px;
    top: 262px;
    margin: 0;
    color: var(--navy);
    font-weight: 700;
    font-size: 60px;
    line-height: 60px;
    letter-spacing: 2px;
    text-transform: uppercase;
  }
  .features {
    position: absolute;
    left: 48px;
    top: 398px;
    margin: 0;
    padding: 0;
    list-style: none;
  }
  .features li {
    display: flex;
    align-items: center;
    height: 48px;
    color: var(--white);
    font-weight: 700;
    font-size: 35px;
    letter-spacing: 1.5px;
    text-transform: uppercase;
  }
  .features li::before {
    content: "";
    width: 10px;
    height: 10px;
    margin: 0 18px 8px 5px;
    border: 3px solid var(--white);
    transform: rotate(45deg);
    flex-shrink: 0;
  }
  .brand-corner {
    position: absolute;
    left: 1010px;
    top: 90px;
    width: 176px;
    display: flex;
    flex-direction: column;
    align-items: center;
    gap: 26px;
  }
  .brand-corner .mark {
    width: 96px;
    height: 96px;
    background: var(--white);
  }
  .brand-corner .name {
    color: var(--white);
    font-weight: 700;
    font-size: 25px;
    letter-spacing: 1px;
  }
  .contact-band {
    position: absolute;
    left: 0;
    top: 635px;
    width: 1200px;
    height: 140px;
    background: var(--magenta);
    display: flex;
    align-items: center;
  }
  .company {
    display: flex;
    align-items: center;
    margin-left: 30px;
    gap: 14px;
  }
  .company .mark {
    width: 64px;
    height: 64px;
    background: var(--white);
  }
  .company .details {
    color: var(--white);
    font-weight: 600;
  }
  .company .name {
    font-size: 15px;
    padding-bottom: 5px;
    border-bottom: 1.5px solid var(--white);
    white-space: nowrap;
  }
  .company .web {
    font-size: 12px;
    padding-top: 5px;
  }
  .phone {
    margin: 0 0 0 28px;
    color: var(--white);
    font-weight: 700;
    font-size: 50px;
    letter-spacing: 2px;
    text-transform: uppercase;
    white-space: nowrap;
    padding-top: 8px;
  }
</style>
</head>
<body>
<div class="sign">
  <svg class="backdrop" width="1200" height="800" viewBox="0 0 1200 800" aria-hidden="true">
    <rect width="1200" height="800" fill="var(--sky)"/>
    <polygon points="490,0 822,0 955,165 810,410" fill="var(--sky-light)"/>
    <polygon points="822,0 1062,0 955,165" fill="var(--navy)"/>
    <polygon points="1062,0 1200,0 1200,522 955,165" fill="var(--magenta)"/>
    <polygon points="955,165 1200,522 1200,800 1000,800 1000,635 810,410" fill="var(--mist)"/>
    <polygon points="810,410 1000,635 680,635" fill="var(--white)"/>
    <polygon points="570,800 680,635 1200,635 1200,800" fill="var(--mist)"/>
  </svg>

  <div class="brand-corner">
    <div class="mark"></div>
    <div class="name">BRIGHTLINE</div>
  </div>

  <h1 class="project-title">Meridale<br>Commerce Park</h1>

  <ul class="features">
    <li>Land for Sale</li>
    <li>Build to Suit</li>
    <li>Zoning: Industrial (G I &amp; L I)</li>
  </ul>

  <footer class="contact-band">
    <div class="company">
      <div class="mark"></div>
      <div class="details">
        <div class="name">Brightline Property Partners, Inc.</div>
        <div class="web">www.brightlinepartners.com</div>
      </div>
    </div>
    <p class="phone">Contact us at (415)736-2958</p>
  </footer>
</div>
</body>
</html>
```